Moravel Aesthetic Doctor

I require an elegant, luxurious looking business card for my aesthetic business. I am a doctor and that will set me aside from competitors. I am planning to provide home and spa based treatments to clients with high expectations. I have attached my logo.

```html
<!DOCTYPE html>
<html lang="en">
<head>
<meta charset="utf-8">
<title>Moravel Aesthetic Doctor – Business Card</title>
<link rel="stylesheet" href="https://fonts.googleapis.com/css2?family=Cormorant+Garamond:wght@500;700&family=Questrial&display=swap">
<style>
  :root {
    --backdrop: #5c5f62;
    --card: #ffffff;
    --brand-grey: #8a8c8f;
    --rule-grey: #b4b6b8;
    --brand-blue: #1aa8e6;
    --band-blue: #00aeef;
    --ink-black: #111214;
    --text-grey: #8e9093;
    --white: #ffffff;
  }
  * { margin: 0; padding: 0; box-sizing: border-box; }
  html, body { width: 1200px; height: 965px; overflow: hidden; }
  body {
    background: var(--backdrop);
    display: flex; flex-direction: column; align-items: center; justify-content: center;
    gap: 30px;
    font-family: "Questrial", sans-serif;
  }
  .card {
    position: relative;
    width: 760px; height: 434px;
    background: var(--card);
    overflow: hidden;
    box-shadow: 0 6px 18px rgba(0,0,0,.35);
  }
  /* logo lockup */
  .logo { position: absolute; display: flex; align-items: center; gap: 18px; }
  .logo-mark {
    width: 92px; height: 92px; border-radius: 50%;
    border: 3px solid var(--rule-grey);
    flex: none;
  }
  .logo-name {
    font-family: "Cormorant Garamond", serif; font-weight: 500;
    color: var(--brand-grey);
    font-size: 40px; letter-spacing: 2px; line-height: 1; text-transform: uppercase;
  }
  /* front */
  .card-front .logo { left: 50%; top: 120px; transform: translateX(-50%); }
  .front-rule-top {
    position: absolute; left: 520px; right: 40px; top: 232px;
    height: 1px; background: var(--rule-grey);
  }
  .tagline-row {
    position: absolute; left: 40px; right: 40px; top: 328px;
    display: flex; align-items: center; gap: 16px;
  }
  .tagline-row .rule { flex: 1; height: 1px; background: var(--rule-grey); }
  .tagline {
    font-family: "Cormorant Garamond", serif; font-weight: 700;
    color: var(--brand-blue); font-size: 17px; letter-spacing: 1.5px;
    text-transform: uppercase; white-space: nowrap;
  }
  /* back */
  .card-back .logo { left: 40px; top: 40px; }
  .card-back .logo-mark { width: 80px; height: 80px; }
  .card-back .logo-name { font-size: 34px; }
  .social { position: absolute; right: 34px; top: 34px; display: flex; gap: 10px; }
  .social-dot { width: 18px; height: 18px; border-radius: 50%; background: var(--brand-blue); }
  .doctor { position: absolute; left: 40px; top: 190px; }
  .doctor-line { display: flex; align-items: baseline; gap: 10px; }
  .doctor-name {
    font-family: "Cormorant Garamond", serif; font-weight: 700;
    color: var(--brand-blue); font-size: 36px;
  }
  .doctor-sep { width: 2px; height: 30px; background: var(--ink-black); align-self: center; }
  .doctor-title { color: var(--text-grey); font-size: 19px; letter-spacing: 1px; }
  .doctor-diploma { color: var(--text-grey); font-size: 19px; margin-top: 4px; letter-spacing: .5px; }
  .bands { position: absolute; inset: 0; width: 760px; height: 434px; }
  .services {
    position: absolute; right: 26px; top: 302px;
    color: var(--white); font-size: 18px; line-height: 1.4; text-align: right;
  }
  .contacts {
    position: absolute; left: 40px; top: 356px;
    list-style: none; color: var(--white); font-size: 18px; line-height: 1.35;
  }
  .contacts li { display: flex; align-items: center; gap: 12px; }
  .contacts svg { width: 16px; height: 16px; flex: none; }
</style>
</head>
<body>

<section class="card card-front" aria-label="Card front">
  <div class="logo">
    <span class="logo-mark"></span>
    <span class="logo-name">Moravel Aesthetic Doctor</span>
  </div>
  <div class="front-rule-top"></div>
  <div class="tagline-row">
    <span class="rule"></span>
    <span class="tagline">Home and Spa Based Treatments</span>
    <span class="rule"></span>
  </div>
</section>

<section class="card card-back" aria-label="Card back">
  <svg class="bands" viewBox="0 0 760 434" aria-hidden="true">
    <polygon points="300,290 760,290 760,434 460,434" fill="var(--band-blue)"/>
    <polygon points="0,345 347,345 446,434 0,434" fill="var(--ink-black)"/>
    <rect x="748" y="290" width="12" height="40" fill="var(--ink-black)"/>
  </svg>

  <div class="logo">
    <span class="logo-mark"></span>
    <span class="logo-name">Moravel Aesthetic Doctor</span>
  </div>

  <div class="social" aria-label="Social media">
    <span class="social-dot"></span>
    <span class="social-dot"></span>
  </div>

  <div class="doctor">
    <div class="doctor-line">
      <span class="doctor-name">Dr Elira Voss</span>
      <span class="doctor-sep"></span>
      <span class="doctor-title">MRCPCH MD</span>
    </div>
    <div class="doctor-diploma">Australasian Diploma of Aesthetic Medicine</div>
  </div>

  <p class="services">
    Dermal injectables - Plasma facials - Microneedling<br>
    Skin boosters - Excessive sweating<br>
    Home and Spa Based Treatments
  </p>

  <ul class="contacts">
    <li>
      <svg viewBox="0 0 16 16"><path d="M4 1.5l2.5 3-1.5 1.5a9 9 0 0 0 5 5l1.5-1.5 3 2.5-1.5 2.5C7 14 2 9 1.5 3z" fill="none" stroke="var(--white)" stroke-width="1.2"/></svg>
      0800 555 014
    </li>
    <li>
      <svg viewBox="0 0 16 16"><rect x="1.5" y="3.5" width="13" height="9" fill="none" stroke="var(--white)" stroke-width="1.2"/><path d="M1.5 3.5l6.5 5 6.5-5" fill="none" stroke="var(--white)" stroke-width="1.2"/></svg>
      elira@moravel.co.nz
    </li>
    <li>
      <svg viewBox="0 0 16 16"><circle cx="8" cy="8" r="6.5" fill="none" stroke="var(--white)" stroke-width="1.2"/><ellipse cx="8" cy="8" rx="2.8" ry="6.5" fill="none" stroke="var(--white)" stroke-width="1"/><path d="M1.5 8h13M2.5 5h11M2.5 11h11" stroke="var(--white)" stroke-width="1"/></svg>
      www.moravel.co.nz
    </li>
  </ul>
</section>

</body>
</html>
```